Web Design Project

Brightfold Publishing owns and operates a large number of editorial websites. These websites provides mostly consumers in the financial services space with information and price comparisons for a particular service.

Brightfold Publishing, as the holding company for each of these sites, currently has no website. We need to build a website targeted towards potential partners for our websites. The idea being that when we start a conversation with a partner, they can view our site and obtain some basic information about who we are.

The structure of the site is to be very simple, containing only a brief description about who we are, our contact details and a list of some of our websites:
• CoverVault.net.au
• MotorPolicyCheck.com.au
• DwellingCoverCheck.com.au
• MedicalCoverCheck.com.au
• LegacyCoverCheck.com.au
• JourneyCoverCheck.com.au
• AnimalCoverCheck.com.au
• PrivateLendingCheck.com.au
• MobileCoolingUnit.com.au
• FixedSavingsYield.com.au
• ThriftyHousehold.com.au
• CoinNana.com.au
• TameYourPlastic.com.au
• PurseMinder.com.au
• ThirdPartyClaimsCoverNational.com.au
• Trade-Cover.com.au
• MotorPolicyProviders.com.au
• MedicalCoverProviders.com.au
• DwellingCoverHub.com
• LegacyCoverHub.com
• EarningsShieldCoverHub.com
• MedicalCoverHub.com
• AnimalCoverHub.com
• PrivateLendingHub.com
• ChargePlasticHub.com
• DwellingLendingHub.com
• RetireNestEgg.net.au

The design of the site should say 'Internet company', 'professional', 'fresh thinking'. The design should not look like a corporate site that you would see from any corporate services business with images of people in suits. We are ultimately an Internet business and there should be a unique feel to the site.

We are open to a suggestion of a colour pallet as the holding company does not have an established logo.

Some sites that we like are:

http://www.quillmarsh-studio.co.uk/#home
http://previewbox00.layoutdock.example/wt_52418/index.html
http://previewbox00.layoutdock.example/wordpress_61942/
http://ponderloop.example/
http://www.brindlux.example/
http://www.tobiasvrankel.example/
http://www.slickfrontdoors.example/Corporate/design-ideas-detail.html?id=4197
http://pairmint.example/
http://orvendal.example/

Reason: Hi all, Apologies, but I need to extend the timeline. One of our key stakeholders is away for the next week. There are a few good designs that we have received to date and there are some tweaks that we would like to see before making a final decision. Thank you to everyone that has submitted designs - Have a great new year. Derek

Reason: Sorry to have to delay the deadline on this, but we did not find anything in the designs really resonated with us. We will have a further think about the existing designs that have been submitted and how we can provide more specific feedback to the designers to make some modifications to the designs.

Target Market(s)

We are targeting insurance companies / brokers that we are talking to. The idea is that we show a professional face to them.

Industry/Entity Type

Financial

Requirements
Must have
• Home Page (possibly integrated with About us details)
Contact Us
Our Sites

```html
<!DOCTYPE html>
<html lang="en">
<head>
<meta charset="utf-8">
<title>Contact Us – Brightfold Publishing</title>
<link rel="stylesheet" href="https://fonts.googleapis.com/css2?family=Anton&family=Open+Sans:wght@400;600;700&display=swap">
<style>
  :root {
    --header-top: #003a6b;
    --sky-deep: #1690f5;
    --sky-light: #b8dcfc;
    --page-grey: #c9c9c9;
    --panel: #ffffff;
    --brand-blue: #1a8ef0;
    --wordmark: #ffffff;
    --nav-idle: #a9d5fb;
    --nav-active: #ffffff;
    --ink: #333333;
    --accent-orange: #f7923a;
    --details-bg: #f3f3f3;
    --field-bg: #f4f4f4;
    --field-border: #cfcfcf;
    --button-top: #2ab0ea;
    --button-bottom: #1681c9;
    --footer-top: #07304f;
    --footer-bottom: #000c17;
  }
  * { box-sizing: border-box; margin: 0; padding: 0; }
  html, body { width: 1200px; height: 948px; overflow: hidden; }
  body {
    position: relative;
    font-family: "Open Sans", Verdana, sans-serif;
    color: var(--ink);
    background: var(--page-grey);
  }
  .site-header {
    position: absolute; left: 0; top: 0; width: 1200px; height: 240px;
    background: linear-gradient(to bottom, var(--header-top) 0, var(--header-top) 17px, var(--sky-deep) 17px, #4aa9f6 90px, var(--sky-light) 174px, var(--sky-light) 240px);
  }
  .brand {
    position: absolute; left: 74px; top: 32px;
    display: flex; align-items: center; gap: 10px;
    font-family: "Open Sans", Verdana, sans-serif; font-weight: 600; font-size: 26px;
    color: var(--wordmark); line-height: 1;
  }
  .brand-mark { width: 16px; height: 16px; background: var(--wordmark); }
  .main-nav { position: absolute; left: 74px; top: 83px; display: flex; gap: 38px; }
  .main-nav a {
    font-family: Arial, "Open Sans", sans-serif; font-size: 17px;
    color: var(--nav-idle); text-decoration: none;
  }
  .main-nav a.is-active { color: var(--nav-active); }
  .content-panel {
    position: absolute; left: 24px; top: 174px; width: 1152px; height: 707px;
    background: var(--panel); border-radius: 22px 22px 0 0;
    box-shadow: 0 0 6px rgba(0,0,0,0.25);
  }
  .page-title {
    position: absolute; left: 49px; top: 10px;
    font-family: "Anton", sans-serif; font-weight: 400; font-size: 58px; line-height: 1.2;
    color: var(--brand-blue); letter-spacing: 0.5px;
  }
  .section-title { position: absolute; font-size: 22px; font-weight: 400; color: var(--ink); }
  .details-title { left: 49px; top: 109px; }
  .message-title { left: 576px; top: 109px; }
  .details-card {
    position: absolute; left: 36px; top: 151px; width: 362px; height: 155px;
    background: var(--details-bg); padding: 18px 14px;
    font-size: 17px; line-height: 1.25;
  }
  .details-card .company { color: var(--accent-orange); font-weight: 700; }
  .details-card .line-gap { margin-top: 4px; }
  .contact-form { position: absolute; left: 576px; top: 0; }
  .field-label { position: absolute; left: 0; font-size: 13px; white-space: nowrap; }
  .field {
    position: absolute; left: 0; height: 30px;
    background: var(--field-bg); border: 1px solid var(--field-border);
  }
  .field-short { width: 332px; }
  .field-wide { width: 509px; }
  .field-message { height: 197px; }
  .send-button {
    position: absolute; left: 0; top: 592px; width: 88px; height: 27px;
    border: none; border-radius: 5px;
    background: linear-gradient(to bottom, var(--button-top), var(--button-bottom));
    color: #fff; font-family: Georgia, serif; font-weight: 700; font-size: 13px;
  }
  .site-footer {
    position: absolute; left: 0; top: 881px; width: 1200px; height: 67px;
    background: linear-gradient(to bottom, var(--footer-top), var(--footer-bottom));
  }
  .site-footer p { position: absolute; left: 73px; top: 22px; color: #fff; font-size: 15px; }
</style>
</head>
<body>
  <header class="site-header">
    <div class="brand"><span class="brand-mark"></span>Brightfold Publishing</div>
    <nav class="main-nav">
      <a href="#">Home</a>
      <a href="#">Our Sites</a>
      <a href="#" class="is-active">Contact Us</a>
    </nav>
  </header>

  <main class="content-panel">
    <h1 class="page-title">CONTACT US</h1>

    <h2 class="section-title details-title">Our details</h2>
    <div class="details-card">
      <div class="company">Brightfold Publishing Pty Ltd</div>
      <div>Suite 412, 18 Harlow Street</div>
      <div>Marrick Junction NSW 2090</div>
      <div class="line-gap">T: 02 9000 4417</div>
      <div class="line-gap">E: info [at] brightfoldpublishing.example</div>
    </div>

    <h2 class="section-title message-title">Send us a message</h2>
    <form class="contact-form">
      <label class="field-label" style="top:150px">Contact Name</label>
      <div class="field field-short" style="top:169px"></div>
      <label class="field-label" style="top:218px">Contact E-mail</label>
      <div class="field field-short" style="top:238px"></div>
      <label class="field-label" style="top:286px">Subject</label>
      <div class="field field-wide" style="top:306px"></div>
      <label class="field-label" style="top:353px">Message</label>
      <div class="field field-wide field-message" style="top:373px"></div>
      <button type="button" class="send-button">Send</button>
    </form>
  </main>

  <footer class="site-footer">
    <p>© 2012 Brightfold Publishing</p>
  </footer>
</body>
</html>
```